New letterhead and business cards for dental office

I need a new letterhead, envelopes, and business cards for our 2 dental offices. The letterhead should be able to be used at either office. A professional elegant look is desired.
Exact particulars such as the address, phone numbers etc will be provided later.
***** a reminder: we have 2 separate locations, so the letterhead needs to have 2 sets of addresses, phones numbers, etc.
Our previous letterhead had a check box to indicate which of the two offices we were corresponding from. I would like some creative ideas here.
Dental

```html
<!DOCTYPE html>
<html lang="en">
<head>
<meta charset="utf-8">
<title>Harlow &amp; Birch Family Dental Centres – Letterhead</title>
<link rel="stylesheet" href="https://fonts.googleapis.com/css2?family=Questrial&family=Montserrat:wght@600;700&display=swap">
<style>
  :root {
    --bg: #e9e9ea;
    --paper: #ffffff;
    --brand-blue: #3a78c2;
    --brand-navy: #2b4f96;
    --ink: #3c3c3e;
    --ink-soft: #6a6a6e;
    --deco-tint: #d6e4f5;
  }
  * { margin: 0; padding: 0; box-sizing: border-box; }
  html, body { width: 1200px; height: 936px; overflow: hidden; background: var(--bg); }
  body { font-family: "Questrial", "Century Gothic", sans-serif; color: var(--ink); }

  .letterhead {
    position: absolute; left: 290px; top: 28px;
    width: 620px; height: 878px;
    background: var(--paper);
    box-shadow: 0 2px 10px rgba(0,0,0,.08);
    overflow: hidden;
  }

  .brand { position: absolute; left: 56px; top: 64px; display: flex; align-items: center; gap: 10px; }
  .brand__dot { width: 26px; height: 26px; border-radius: 50%; background: var(--brand-blue); }
  .brand__name { font-size: 19px; color: var(--brand-blue); line-height: 1.15; }
  .brand__name small { display: block; font-size: 8.5px; letter-spacing: 3px; text-transform: uppercase; }

  .side-deco { position: absolute; right: -60px; top: 330px; }

  .letter { position: absolute; left: 56px; top: 200px; width: 420px; font-size: 9.5px; line-height: 1.55; color: var(--ink-soft); }
  .letter__salutation { font-family: "Montserrat", sans-serif; font-weight: 700; font-size: 12px; color: var(--ink); margin-bottom: 8px; }
  .letter p { margin-bottom: 14px; }
  .sign-off { display: flex; align-items: flex-end; gap: 14px; margin-top: 4px; }
  .sign-off__closing { font-size: 9.5px; }
  .sign-off__name { font-family: "Montserrat", sans-serif; font-weight: 700; font-size: 12px; color: var(--ink); }
  .signature { width: 110px; height: 44px; border-radius: 4px; background: linear-gradient(90deg, #e6eef9, #d3e1f4); }

  .offices { position: absolute; left: 56px; right: 56px; bottom: 48px; display: flex; justify-content: space-between; }
  .office__name { font-family: "Montserrat", sans-serif; font-weight: 700; font-size: 7.5px; color: var(--brand-blue); letter-spacing: .4px; text-transform: uppercase; margin-bottom: 4px; }
  .office__body { display: flex; gap: 8px; font-size: 7.5px; line-height: 1.5; color: var(--ink-soft); }
  .office__phones { padding-right: 8px; border-right: 1px solid #bfc3c9; }
  .office__phones span { display: flex; align-items: center; gap: 3px; }
  .office__addr { text-transform: uppercase; }
  .icon { width: 7px; height: 7px; fill: var(--brand-navy); }
</style>
</head>
<body>
  <main class="letterhead">
    <header class="brand">
      <span class="brand__dot"></span>
      <span class="brand__name">Harlow &amp; Birch<small>Family Dental Centres</small></span>
    </header>

    <svg class="side-deco" width="130" height="130" viewBox="0 0 130 130" aria-hidden="true">
      <circle cx="65" cy="65" r="62" fill="var(--deco-tint)"/>
    </svg>

    <article class="letter">
      <p class="letter__salutation">Dear sir / madame,</p>
      <p>Lorem ipsum dolor sit amet, consectetur adipisicing elit, sed do eiusmod tempor incididunt ut labore et dolore magna aliqua. Ut enim ad minim veniam, quis nostrud exercitation ullamco laboris nisi ut aliquip ex ea commodo consequat. Duis aute irure dolor in reprehenderit in voluptate velit esse cillum dolore eu fugiat nulla pariatur. Excepteur sint occaecat cupidatat non proident, sunt in culpa qui officia deserunt mollit anim id est laborum. Lorem ipsum dolor sit amet, consectetur adipisicing elit, sed do eiusmod tempor incididunt ut labore et dolore magna aliqua. Ut enim ad minim veniam, quis nostrud exercitation ullamco laboris nisi ut aliquip ex ea commodo consequat. Duis aute irure dolor in reprehenderit in voluptate velit esse cillum dolore eu fugiat nulla pariatur. Excepteur sint occaecat cupidatat non proident, sunt in culpa qui officia deserunt mollit anim id est laborum.</p>
      <p>Lorem ipsum dolor sit amet, consectetur adipisicing elit, sed do eiusmod tempor incididunt ut labore et dolore magna aliqua. Ut enim ad minim veniam, quis nostrud exercitation ullamco laboris nisi ut aliquip ex ea commodo consequat. Duis aute irure dolor in reprehenderit in voluptate velit esse cillum dolore eu fugiat nulla pariatur. Excepteur sint occaecat cupidatat non proident, sunt in culpa qui officia deserunt mollit anim id est laborum.</p>
      <div class="sign-off">
        <div>
          <div class="sign-off__closing">Yours Sincerely,</div>
          <div class="sign-off__name">Lena Carrow</div>
        </div>
        <div class="signature" role="img" aria-label="Handwritten signature of Lena Carrow"></div>
      </div>
    </article>

    <footer class="offices">
      <section class="office">
        <h3 class="office__name">Harlow Family Dental Centre</h3>
        <div class="office__body">
          <div class="office__phones">
            <span><svg class="icon" viewBox="0 0 10 10"><path d="M2 0.5l2 2-1 1.2c.6 1.3 1.6 2.3 2.9 2.9l1.2-1 2 2-1.3 1.7C4.5 9 1 5.5.3 1.8z"/></svg>555-014-2257</span>
            <span><svg class="icon" viewBox="0 0 10 10"><rect x="1" y="3" width="8" height="5" rx="1"/><rect x="3" y="1" width="4" height="2"/></svg>555-014-2258</span>
          </div>
          <div class="office__addr">1820 Cedar St.<br>Harlow, ON</div>
        </div>
      </section>
      <section class="office">
        <h3 class="office__name">Birch Family Dental Centre</h3>
        <div class="office__body">
          <div class="office__phones">
            <span><svg class="icon" viewBox="0 0 10 10"><path d="M2 0.5l2 2-1 1.2c.6 1.3 1.6 2.3 2.9 2.9l1.2-1 2 2-1.3 1.7C4.5 9 1 5.5.3 1.8z"/></svg>555-016-3638</span>
            <span><svg class="icon" viewBox="0 0 10 10"><rect x="1" y="3" width="8" height="5" rx="1"/><rect x="3" y="1" width="4" height="2"/></svg>555-016-3639</span>
          </div>
          <div class="office__addr">4075 Meadow Farm Dr.<br>Birchton, ON</div>
        </div>
      </section>
    </footer>
  </main>
</body>
</html>
```